Brackwell Exteriors Needs a New Website!

We are an exteriors company specializing in vinyl siding, Corwin Maddox siding, aluminum soffit/fascia, trough. We do new construction work as well as renovations. We also build detached garages.
You can view our current website at www.brackwellfabricators.ca
I want to completely overhaul the website.
Our services are different now as we no longer do new home construction as well as we do not do the snow clearing.
I want to focus on 2 things in particular on the website:

1/ Exterior renovations

2/ Detached Garage construction.

I have included our logo in the attached files to use as well.

Some features we would like:

1/ Be able to easily attach a video from Clipverse/Reelio to highlight a product or service
2/ Quick chat or contact button that we can talk to a potential client quickly
3/ Meet the Team page that is interesting and fresh
4/ Place for us to put in helpful exterior tips/suggestions for homeowners.

Content is not important, but looking for the best design that will attract people once they click on our page and want to renovate with us.

Target Market(s)

People looking for renovations on their home, people looking to build a detached garage.

Industry/Entity Type

Residential Construction

Number of Pages Required

5+ page

Font styles to use
Sans Serif

Requirements
Must have
• Fresh and exciting home page.

Simple design. Don't want it over complicated or too much information to confuse the potential client.

Easy way to contact us.

Meet the team page that instills confidence
Nice to have
• Colour of website to go off our logo. Doesn't need to be an exact match, but something that goes well with our blue and grey.

```html
<!DOCTYPE html>
<html lang="en">
<head>
<meta charset="utf-8">
<title>Brackwell Exteriors</title>
<link href="https://fonts.googleapis.com/css2?family=Montserrat:wght@400;500;600;700;800&display=swap" rel="stylesheet">
<style>
:root{
  --blue:#0b6cc1;
  --blue-deep:#0757a3;
  --blue-light:#e9f3fc;
  --bg:#f4f9fe;
  --ink:#1b1d21;
  --muted:#6a6f78;
  --dark-icon:#2b2d31;
  --white:#ffffff;
}
*{margin:0;padding:0;box-sizing:border-box}
html,body{width:1200px;height:5111px;overflow:hidden}
body{font-family:"Montserrat",sans-serif;color:var(--ink);background:var(--bg)}
.page{position:relative;width:1200px;height:5111px;overflow:hidden;background:var(--bg)}
.abs{position:absolute}
a{color:inherit;text-decoration:none}

/* background waves */
.bg-shapes{position:absolute;left:0;top:0;width:1200px;height:5111px}

/* header */
.brand{position:absolute;left:139px;top:20px;display:flex;align-items:center;gap:12px}
.brand-dot{width:48px;height:48px;border-radius:50%;background:var(--blue)}
.brand-name{font-weight:700;font-size:22px;color:var(--blue);letter-spacing:.5px}
.nav{position:absolute;top:37px;left:0;width:1200px;font-size:12.5px;font-weight:500;color:#20242b}
.nav a{position:absolute;white-space:nowrap}
.nav .active{color:var(--blue)}
.nav-underline{position:absolute;left:530px;top:86px;width:70px;height:3px;background:var(--blue)}

/* hero */
.hero-title{position:absolute;top:518px;width:1200px;text-align:center;color:var(--white);font-weight:700;font-size:38px;letter-spacing:1.5px;text-shadow:0 2px 10px rgba(0,0,0,.35)}
.btn{position:absolute;display:flex;align-items:center;justify-content:center;font-weight:700;font-size:12px;letter-spacing:.6px;border-radius:3px}
.btn-blue{background:var(--blue);color:var(--white)}
.btn-white{background:var(--white);color:var(--blue)}

.service-card{position:absolute;top:654px;width:438px;height:288px;border-radius:6px;overflow:hidden;box-shadow:0 10px 24px rgba(0,40,90,.25)}
.service-card .photo{position:absolute;inset:0}
.service-card .shade{position:absolute;inset:0;background:linear-gradient(to bottom,rgba(0,0,0,0) 40%,rgba(0,0,0,.75))}
.service-card h3{position:absolute;bottom:18px;width:100%;text-align:center;color:var(--white);font-size:21px;font-weight:600;letter-spacing:1.5px;line-height:32px}

/* section headings */
.h-section{font-weight:800;font-size:28px;letter-spacing:.8px;color:var(--ink)}
.h-section span{color:var(--blue)}

/* about */
.about-title{left:143px;top:1018px}
.about-lead{left:143px;top:1082px;width:450px;font-size:13px;line-height:25px;color:#2a2d33}
.about-text{left:143px;top:1143px;width:444px;font-size:12px;line-height:24px;color:var(--muted);letter-spacing:.2px}
.about-photo{left:631px;top:998px;width:424px;height:424px;border-radius:50%;overflow:hidden;border:5px solid var(--white);box-shadow:0 10px 30px rgba(0,40,90,.2)}

/* video */
.video{left:143px;top:1527px;width:912px;height:446px;background:var(--white);padding:8px;box-shadow:0 6px 20px rgba(0,40,90,.12)}
.video .frame{position:relative;width:100%;height:100%;overflow:hidden}
.play{position:absolute;left:422px;top:188px;width:68px;height:68px;border-radius:50%;background:var(--white);display:flex;align-items:center;justify-content:center;box-shadow:0 4px 14px rgba(0,0,0,.25)}
.progress{position:absolute;left:8px;top:392px;width:880px;height:6px;border-radius:3px;background:rgba(255,255,255,.9)}
.progress .fill{position:absolute;left:0;top:0;width:138px;height:6px;border-radius:3px;background:var(--blue)}
.progress .knob{position:absolute;left:130px;top:-5px;width:16px;height:16px;border-radius:50%;background:var(--white);border:3px solid var(--blue)}

/* why choose us */
.why-title{top:2052px;width:1200px;text-align:center}
.feature{position:absolute;width:300px}
.feature h4{font-size:16px;font-weight:700;letter-spacing:.4px;margin-bottom:6px}
.feature p{font-size:12px;line-height:21px;color:var(--muted)}
.feature.left{text-align:right}
.feature.hl h4{color:var(--blue)}
.f-icon{position:absolute;width:80px;height:80px;border-radius:50%;background:var(--dark-icon);display:flex;align-items:center;justify-content:center;box-shadow:0 6px 14px rgba(0,0,0,.2)}
.f-icon.blue{background:var(--blue)}
.hub-outer{left:481px;top:2212px;width:236px;height:236px;border-radius:50%;background:#d6e7f6}
.hub-inner{left:502px;top:2233px;width:194px;height:194px;border-radius:50%;background:var(--white);display:flex;align-items:center;justify-content:center}
.hub-mark{width:92px;height:92px;border-radius:50%;border:8px solid var(--blue)}

/* banners */
.banner{position:absolute;left:141px;width:918px;height:280px;border-radius:10px;overflow:hidden;text-align:center;color:var(--white)}
.banner .bg{position:absolute;inset:0}
.banner .kicker{position:absolute;width:100%;font-size:17px;font-weight:500}
.banner h2{position:absolute;width:100%;font-size:32px;font-weight:700;letter-spacing:1px}

/* featured */
.feat-title{top:2980px;width:1200px;text-align:center}
.feat-line{left:508px;top:3024px;width:80px;height:3px;background:var(--blue)}
.tile{position:absolute;overflow:hidden}
.quality-card{position:absolute;left:143px;top:3264px;width:448px;height:401px;background:linear-gradient(160deg,#1c86d6,#0b5aa6);color:var(--white);text-align:center}
.quality-card .inset{position:absolute;left:12px;top:12px;right:12px;bottom:12px;border:1px solid rgba(255,255,255,.45)}
.quality-card h3{position:absolute;top:114px;width:100%;font-size:18px;font-weight:700;line-height:32px}
.quality-card p{position:absolute;top:202px;left:60px;width:328px;font-size:12px;line-height:21px;color:rgba(255,255,255,.85)}

/* inquiry */
.inquiry{left:141px;top:4105px;width:918px;height:486px;background:var(--white);border-radius:6px;box-shadow:0 14px 40px rgba(0,40,90,.12);border-bottom:5px solid var(--blue)}
.inq-title{top:4176px;width:1200px;text-align:center;font-size:26px}
.field{position:absolute;border:1px solid #e1e5ea;background:var(--white);font-size:11px;color:#8a8f97;padding:12px 12px;font-family:inherit}
.chat{left:1114px;top:4303px;width:60px;height:60px;border-radius:50%;background:var(--white);box-shadow:0 4px 16px rgba(0,40,90,.25);display:flex;align-items:center;justify-content:center}

/* footer */
.footer-brand{position:absolute;left:0;top:4690px;width:1200px;display:flex;justify-content:center;align-items:center;gap:14px}
.footer-brand .brand-dot{background:var(--white);width:64px;height:64px}
.footer-brand .brand-name{color:var(--white);font-size:30px}
.foot-nav{position:absolute;top:4811px;left:0;width:1200px;display:flex;justify-content:center;font-size:12.5px;color:var(--white);font-weight:500}
.foot-nav a{padding:0 24px;border-left:1px solid rgba(255,255,255,.35)}
.foot-nav a:first-child{border-left:none}
.contact-col{position:absolute;top:4880px;width:280px;text-align:center;color:var(--white)}
.contact-col svg{display:block;margin:0 auto 16px}
.contact-col h5{font-size:13px;font-weight:700;letter-spacing:.5px;margin-bottom:6px}
.contact-col p{font-size:11.5px;line-height:18px;color:rgba(255,255,255,.9)}
.copyright{position:absolute;left:0;top:5067px;width:1200px;height:44px;background:var(--white)}
.copyright p{position:absolute;left:143px;top:15px;font-size:11px;color:#3a3e45}
.socials{position:absolute;left:921px;top:8px;display:flex;gap:9px}
.socials span{width:28px;height:28px;border-radius:50%;display:block}
</style>
</head>
<body>
<div class="page">

  <!-- background decoration -->
  <svg class="bg-shapes" viewBox="0 0 1200 5111" aria-hidden="true">
    <defs>
      <linearGradient id="wave" x1="0" y1="0" x2="1" y2="1">
        <stop offset="0" stop-color="#e6f1fb"/><stop offset="1" stop-color="#f4f9fe" stop-opacity="0"/>
      </linearGradient>
      <linearGradient id="foot" x1="0" y1="0" x2="0" y2="1">
        <stop offset="0" stop-color="#1a7fd6"/><stop offset="1" stop-color="#0b65bb"/>
      </linearGradient>
    </defs>
    <path d="M600 1380 C 900 1300 1100 1500 1200 1700 L1200 1200 C1000 1250 800 1330 600 1380Z" fill="url(#wave)"/>
    <path d="M0 2420 C 250 2560 500 2600 800 2560 C1000 2530 1150 2480 1200 2450 L1200 2620 L0 2620Z" fill="#e9f3fc" opacity=".7"/>
    <path d="M0 4472 L1200 4265 L1200 5067 L0 5067Z" fill="url(#foot)"/>
    <path d="M0 4530 L1200 4330" stroke="#3a95e0" stroke-width="40" opacity=".25"/>
  </svg>

  <!-- hero -->
  <svg class="abs" style="left:0;top:0" width="1200" height="870" viewBox="0 0 1200 870" role="img" aria-label="Photo of a two-storey home with grey siding, cedar shake gables and snow on the roof">
    <defs>
      <linearGradient id="heroPhoto" x1="0" y1="0" x2="0" y2="1">
        <stop offset="0" stop-color="#b7c6d8"/>
        <stop offset=".35" stop-color="#6e7b8c"/>
        <stop offset=".7" stop-color="#3c4452"/>
        <stop offset="1" stop-color="#2a2f38"/>
      </linearGradient>
    </defs>
    <polygon points="0,0 1200,0 1200,655 0,866" fill="url(#heroPhoto)"/>
    <polygon points="0,0 1200,0 1200,90 0,90" fill="#ffffff" opacity=".55"/>
  </svg>

  <div class="brand">
    <span class="brand-dot"></span>
    <span class="brand-name">Brackwell Exteriors</span>
  </div>
  <nav class="nav">
    <a class="active" style="left:543px">HOME</a>
    <a style="left:619px">ABOUT US</a>
    <a style="left:724px">SERVICES</a>
    <a style="left:825px">MEET THE TEAM</a>
    <a style="left:971px">CONTACT US</a>
  </nav>
  <div class="nav-underline"></div>

  <h1 class="hero-title">EXPERIENCE THE BRACKWELL DIFFERENCE</h1>
  <a class="btn btn-blue" style="left:512px;top:579px;width:176px;height:36px">GET STARTED TODAY</a>

  <div class="service-card" style="left:151px">
    <div class="photo" role="img" aria-label="Photo of a house under exterior renovation with scaffolding" style="background:linear-gradient(160deg,#b9c8d6 0%,#c9a982 45%,#8a6d52 80%,#3b3128 100%)"></div>
    <div class="shade"></div>
    <h3>EXTERIOR<br>RENOVATIONS</h3>
  </div>
  <div class="service-card" style="left:611px">
    <div class="photo" role="img" aria-label="Photo of a finished two-storey home with a detached garage" style="background:linear-gradient(160deg,#9fc1e0 0%,#c7a48d 45%,#9a7660 78%,#3b3129 100%)"></div>
    <div class="shade"></div>
    <h3>DETACHED GARAGE<br>CONSTRUCTION</h3>
  </div>

  <!-- about -->
  <h2 class="abs h-section about-title">ABOUT <span>US</span></h2>
  <p class="abs about-lead">We Are A People Looking For Renovations On Their Home,<br>People Looking To Build A Detached Garage</p>
  <p class="abs about-text">Lorem ipsum dolor sit amet, consectetuer adipiscing elit, sed diam nonummy nibh euismod tincidunt ut laoreet dolore magna aliquam erat volutpat. Ut wisi enim ad minim veniam, quis nostrud exerci tation ullamcorper suscipit lobortis nisl ut aliquip ex ea commodo consequat. Duis autem vel eum iriure dolor in hendrerit in vulputate velit esse molestie consequat, vel illum dolore eu feugiat nulla facilisis at vero eros et accumsan et iusto odio dignissim qui blandit praesent luptatum zzril delenit augue duis dolore te feugait nulla facilisi.vel illumet iusto odio dignissim...</p>
  <a class="btn btn-blue" style="left:141px;top:1384px;width:143px;height:38px">GET STARTED</a>
  <svg class="abs" style="left:284px;top:1340px" width="420" height="120" viewBox="0 0 420 120" aria-hidden="true">
    <path d="M2 64 C 80 110 170 100 210 80 C 250 60 230 40 200 60 C 180 75 220 90 270 70 C 320 50 360 30 405 22" fill="none" stroke="#9fb8d0" stroke-width="1.2" stroke-dasharray="3 3"/>
    <path d="M400 16 L410 22 L400 28" fill="none" stroke="#0b6cc1" stroke-width="1.5"/>
  </svg>
  <div class="abs about-photo" role="img" aria-label="Photo of a modern home with glass balconies and a landscaped front yard" style="background:linear-gradient(170deg,#8fb3d6 0%,#d7dde2 40%,#8a8f92 70%,#5d7c4a 100%)"></div>

  <!-- video -->
  <div class="abs video">
    <div class="frame" role="img" aria-label="Video still of scaffolding alongside a house with new siding" style="background:linear-gradient(150deg,#c3cad3 0%,#8f98a4 45%,#6f5b4c 75%,#b7bfc8 100%)">
      <div class="play">
        <svg width="24" height="26" viewBox="0 0 24 26"><path d="M4 2 L22 13 L4 24Z" fill="#0b6cc1"/></svg>
      </div>
      <div class="progress"><div class="fill"></div><div class="knob"></div></div>
    </div>
  </div>

  <!-- why choose us -->
  <h2 class="abs h-section why-title">WHY <span>CHOOSE US?</span></h2>
  <svg class="abs" style="left:349px;top:2080px" width="500" height="500" viewBox="0 0 500 500" aria-hidden="true">
    <circle cx="250" cy="250" r="188" fill="none" stroke="#9aa5b1" stroke-width="1" stroke-dasharray="3 4"/>
    <path d="M244 66 L250 70 L244 74" fill="none" stroke="#6a6f78" stroke-width="1.4"/>
    <path d="M256 426 L250 430 L256 434" fill="none" stroke="#6a6f78" stroke-width="1.4"/>
  </svg>
  <div class="abs hub-outer"></div>
  <div class="abs hub-inner"><span class="hub-mark"></span></div>

  <div class="feature left" style="left:124px;top:2148px">
    <h4>GUARANTEED SATISFACTION</h4>
    <p>We aren't happy unless you are. Along with a robust limited lifetime warranty on our work, we ensure you are satisfied even years after completion.</p>
  </div>
  <div class="feature left" style="left:62px;top:2288px">
    <h4>SAFETY CONSCIENCE</h4>
    <p>COR certification, liability insurance, and WCB coverage on all workers gives you peace of mind that the job will be done safely.</p>
  </div>
  <div class="feature left" style="left:124px;top:2431px">
    <h4>UNRIVALLED QUALITY</h4>
    <p>Our greatest asset is our unrivalled pursuit of a "top of the line" job each and every time.</p>
  </div>
  <div class="feature hl" style="left:773px;top:2148px">
    <h4>CERTIFIED EXPERIENCE</h4>
    <p>Having professionals do the job gives you the confidence that the job will be done right, on budget, and on time.</p>
  </div>
  <div class="feature" style="left:837px;top:2288px">
    <h4>SUPERIOR COMMUNICATION</h4>
    <p>Taking the time to explain the construction process and promptly answering the phone or email is what sets us apart from others.</p>
  </div>
  <div class="feature" style="left:773px;top:2431px">
    <h4>COMPETITIVE PRICING</h4>
    <p>Although we offer the best in services, we won't blow your budget on the job. We also take credit cards in our renovations division.</p>
  </div>

  <div class="f-icon" style="left:436px;top:2151px">
    <svg width="34" height="34" viewBox="0 0 34 34" fill="none" stroke="#fff" stroke-width="2"><rect x="4" y="5" width="26" height="20" rx="2"/><path d="M10 30h14M17 25v5M10 15l4 4 9-9"/></svg>
  </div>
  <div class="f-icon" style="left:374px;top:2290px">
    <svg width="34" height="34" viewBox="0 0 34 34" fill="none" stroke="#fff" stroke-width="2"><path d="M17 3 L29 8 V16 C29 24 23 29 17 31 C11 29 5 24 5 16 V8Z"/><path d="M11 17l4 4 8-8"/></svg>
  </div>
  <div class="f-icon" style="left:436px;top:2431px">
    <svg width="34" height="34" viewBox="0 0 34 34" fill="none" stroke="#fff" stroke-width="2"><circle cx="17" cy="14" r="9"/><path d="M12 22l-3 9 8-4 8 4-3-9"/></svg>
  </div>
  <div class="f-icon blue" style="left:680px;top:2151px">
    <svg width="34" height="34" viewBox="0 0 34 34" fill="none" stroke="#fff" stroke-width="2"><rect x="5" y="4" width="24" height="26" rx="2"/><path d="M10 11h14M10 17h14M10 23h8"/></svg>
  </div>
  <div class="f-icon" style="left:741px;top:2290px">
    <svg width="34" height="34" viewBox="0 0 34 34" fill="none" stroke="#fff" stroke-width="2"><path d="M5 6h18v12H12l-5 4v-4H5Z"/><path d="M25 12h4v12h-2v4l-5-4h-8v-3"/></svg>
  </div>
  <div class="f-icon" style="left:680px;top:2431px">
    <svg width="34" height="34" viewBox="0 0 34 34" fill="none" stroke="#fff" stroke-width="2"><circle cx="17" cy="17" r="12"/><path d="M21 12c-1-1.5-6-2-6 1s6 2 6 5-5 3-7 1M17 9v3M17 22v3"/></svg>
  </div>

  <!-- pride banner -->
  <section class="banner" style="top:2632px">
    <div class="bg" role="img" aria-label="Blue background with a faint architectural blueprint" style="background:linear-gradient(135deg,#1d86d8,#0a5ea9)"></div>
    <p class="kicker" style="top:77px">Honest And Reliable Construction Service In Edmonton And Area.</p>
    <h2 style="top:108px">We Take Pride In Each And Every Project</h2>
    <a class="btn btn-white" style="left:371px;top:170px;width:176px;height:36px">GET STARTED TODAY</a>
  </section>

  <!-- featured work -->
  <h2 class="abs h-section feat-title">FEATURED <span>WORK</span></h2>
  <div class="abs feat-line"></div>

  <div class="tile" style="left:143px;top:3056px;width:216px;height:190px;background:linear-gradient(170deg,#b9c6d2,#8c7a6a 65%,#5b5044)" role="img" aria-label="Photo of a new home under construction"></div>
  <div class="tile" style="left:373px;top:3056px;width:218px;height:190px;background:linear-gradient(170deg,#f4f4f4,#dcdcdc)" role="img" aria-label="Floor plan drawing of a house"></div>
  <div class="tile" style="left:607px;top:3056px;width:450px;height:398px;background:linear-gradient(175deg,#2d4a72 0%,#6d7f96 35%,#a5734a 65%,#3f5a2e 100%)" role="img" aria-label="Photo of a modern wood-clad home at dusk"></div>
  <div class="quality-card">
    <div class="inset"></div>
    <h3>Unrivalled Quality and Attention to<br>Detail Turning Dreams into Reality</h3>
    <p>Lorem ipsum dolor sit amet, ipsu, ofte consectetuer adipiscing elit, sed diam nonummy nibh euismod tincidunt ut laoreet dolore magna aliquam erat volutpat Ut wisi enim...</p>
  </div>
  <div class="tile" style="left:607px;top:3472px;width:216px;height:193px;background:linear-gradient(160deg,#d8d2c8,#9d7a5a 55%,#5a4333)" role="img" aria-label="Photo of interior wooden staircase framing"></div>
  <div class="tile" style="left:841px;top:3472px;width:216px;height:193px;background:linear-gradient(160deg,#eceae6,#b9b5ae 55%,#7d7973)" role="img" aria-label="Photo of a renovated grey kitchen"></div>

  <!-- garage banner -->
  <section class="banner" style="top:3754px">
    <div class="bg" role="img" aria-label="Photo of a dark detached garage with a house behind it" style="background:linear-gradient(170deg,#2c3a4a,#4b4a48 55%,#2a2520)"></div>
    <div class="bg" style="background:rgba(10,20,35,.35)"></div>
    <p class="kicker" style="top:78px">Lorem ipsum dolor sit amet, Ipsum often consectetuer adipiscing elit</p>
    <h2 style="top:110px">DETACHED GARAGE CONSTRUCTION</h2>
    <a class="btn btn-white" style="left:371px;top:170px;width:176px;height:36px">GET STARTED TODAY</a>
  </section>

  <!-- inquiry -->
  <div class="abs inquiry"></div>
  <h2 class="abs h-section inq-title">QUICK <span>INQUIRY</span></h2>
  <div class="field" style="left:200px;top:4248px;width:389px;height:40px">Name*</div>
  <div class="field" style="left:611px;top:4248px;width:387px;height:40px">Phone*</div>
  <div class="field" style="left:200px;top:4305px;width:389px;height:40px">Email*</div>
  <div class="field" style="left:611px;top:4305px;width:387px;height:40px">Choose a Service
    <svg style="position:absolute;right:12px;top:16px" width="10" height="7" viewBox="0 0 10 7"><path d="M1 1l4 4 4-4" fill="none" stroke="#6a6f78" stroke-width="1.4"/></svg>
  </div>
  <div class="field" style="left:200px;top:4363px;width:798px;height:100px">Message*</div>
  <a class="btn btn-blue" style="left:535px;top:4480px;width:128px;height:36px">SUBMIT</a>

  <div class="abs chat">
    <svg width="30" height="30" viewBox="0 0 30 30" fill="none" stroke="#0b6cc1" stroke-width="2"><path d="M4 5h15v10H10l-4 4v-4H4Z"/><path d="M21 11h5v10h-2v4l-4-4h-6v-3"/></svg>
  </div>

  <!-- footer -->
  <div class="footer-brand">
    <span class="brand-dot"></span>
    <span class="brand-name">Brackwell Exteriors</span>
  </div>
  <nav class="foot-nav">
    <a>HOME</a><a>ABOUT US</a><a>SERVICES</a><a>MEET THE TEAM</a><a>CONTACT US</a>
  </nav>

  <div class="contact-col" style="left:146px">
    <svg width="26" height="40" viewBox="0 0 26 40" fill="none" stroke="#fff" stroke-width="2"><rect x="2" y="2" width="22" height="36" rx="3"/><path d="M10 33h6"/></svg>
    <h5>PHONE</h5>
    <p>+1 780-555-0148</p>
  </div>
  <div class="contact-col" style="left:461px">
    <svg width="30" height="40" viewBox="0 0 30 40" fill="none" stroke="#fff" stroke-width="2"><path d="M15 38 C 6 26 3 20 3 14 A12 12 0 0 1 27 14 C27 20 24 26 15 38Z"/><circle cx="15" cy="14" r="4"/></svg>
    <h5>BRACKWELL EXTERIORS</h5>
    <p>4820 Alder Ridge Rd #118, Sherwood<br>Park, AB T8B 0X2, Canada</p>
  </div>
  <div class="contact-col" style="left:772px">
    <svg width="44" height="40" viewBox="0 0 44 40" fill="none" stroke="#fff" stroke-width="2"><rect x="2" y="6" width="40" height="28"/><path d="M2 6l20 16 20-16M2 34l15-14M42 34L27 20"/></svg>
    <h5>EMAIL</h5>
    <p>info@brackwellfabricators.ca</p>
  </div>

  <div class="copyright">
    <p>Copyright © 2020 BRACKWELL EXTERIORS. All Rights Reserved.</p>
    <div class="socials">
      <span style="background:#1f5fb4" aria-label="Social link one"></span>
      <span style="background:#2b8ee0" aria-label="Social link two"></span>
      <span style="background:#1a6fae" aria-label="Social link three"></span>
      <span style="background:#b8388e" aria-label="Social link four"></span>
    </div>
  </div>

</div>
</body>
</html>
```